Bright and beautiful business card for a coach

I'm a personal and business coach based in Perth, Australia. I need a business card that whilst subtle and elegant, will stand out and appeal on a table full of cards.

My business name is Fern Mentoring and the business card must represent the warmth and brightness implied in the name, without being gimmicky. It must have a warmth and appeal and be easy to read.

I prefer clean, minimalist designs.

It must align with the feel of my website and socials: https://www.fernmentoring-example.com.au/
https://www.instagram.com/fernmentoringau/
https://www.facebook.com/fernmentoringau
Updates

Hi Designers Thank you so much for taking the time to submit designs. I wonder if I could have explained myself a little better. Most of the designs that have been submitted look rather formal and many have quite corporate looking embellishments on them (to my eye). I would like softer, warmer, more organic. I’m open to people playing about and being more abstract, using softer embellishments (e.g the line drawing flowers and grasses I’ve used in my socials) incorporating other colours from my palette or like the social icons in my email signature (in PDF), perhaps playing with size/oversize, playing with the bleed. Please don’t be constrained by what I’ve already done, it merely needs to compliment. I’m sorry if I’m not using the right words or have led you astray. I’m no designer, but I’ve done my website, socials, email signature etc all myself (my logo was a design contest) and I was really hoping for my business card to be something more creative than I could have made with a template. Reminder: No black cards/sides please. Thank you 😊

Target Market(s)

Individuals, most likely but not all female. Creative thinkers. Likely professionals.

Industry/Entity Type

Business & Personal Coach

Contact Information for Business Card

(Fern Mentoring Logo) Name: Greta Pellham; Title: Business & Personal Coach; Phone number: +61 (0)491 570 156; Email: greta@fernmentoring-example.com.au; Website: https://fernmentoring-example.com.au; Social icons for Facebook, Instagram & LinkedIn: @fernmentoringAU. Optional strapline: "A steady partner to help you find clarity and focus"

Font styles to use
Sans Serif

Colors
00AB8E
00BBA5
67D7C9
C6EFE9
E9F9F6
59FF00
82FF00
B8FF75
E3FFCB
F4FFEA
FFC000
F8CF3A
FAE287
FDF2CF
FEFAEE

Requirements
Must have
• Must align with feel of my website and socials. Must have a pop of #FFC000 (possibly whole of one side, or at least a block). Bright or white background. Easy to read.
Nice to have
• Possibly incorporate the sunshine/grass picture I have used in website and socials - will upload.
Should not have
• Must not be black or dark. Not impersonal or corporate looking.

```html
<!DOCTYPE html>
<html lang="en">
<head>
<meta charset="utf-8">
<title>Fern Mentoring – Business Card</title>
<link rel="stylesheet" href="https://fonts.googleapis.com/css2?family=Poppins:wght@400;500&family=Allura&display=swap">
<style>
  :root {
    --page-bg: #d9dcde;
    --sun-yellow: #fdc315;
    --gold-dark: #bc7528;
    --gold-mid: #d99a2a;
    --gold-light: #fbc117;
    --card-white: #ffffff;
    --text-grey: #7f8185;
    --rule-grey: #9a9a9a;
  }
  * { box-sizing: border-box; margin: 0; padding: 0; }
  html, body {
    width: 1200px; height: 928px; overflow: hidden;
    background: var(--page-bg);
    font-family: "Poppins", sans-serif;
  }
  .card {
    position: absolute; left: 264px; width: 674px; height: 386px;
    border-radius: 16px; overflow: hidden;
  }
  .card-front { top: 58px; background: var(--sun-yellow); }
  .card-back { top: 484px; background: var(--card-white); }

  .front-wordmark {
    position: absolute; inset: 0;
    display: flex; align-items: center; justify-content: center;
    font-weight: 500; font-size: 46px; letter-spacing: 3px;
    color: var(--gold-dark);
  }

  .back-wordmark {
    position: absolute; left: 38px; top: 97px; width: 272px; height: 114px;
    display: flex; align-items: center; justify-content: center;
    font-weight: 500; font-size: 32px; line-height: 1.1; letter-spacing: 1px;
    color: var(--gold-mid); white-space: nowrap;
  }

  .social-row {
    position: absolute; left: 62px; top: 262px;
    display: flex; align-items: center; gap: 8px;
  }
  .social-dot {
    width: 25px; height: 25px; border-radius: 50%;
    background: linear-gradient(135deg, var(--gold-light), var(--gold-dark));
  }
  .social-handle { margin-left: 4px; font-size: 15.5px; color: var(--text-grey); }

  .divider {
    position: absolute; left: 336px; top: 97px; width: 1px; height: 190px;
    background: var(--rule-grey);
  }
  .divider-accent {
    position: absolute; left: 334.5px; top: 140px; width: 4px; height: 101px;
    background: linear-gradient(180deg, var(--gold-light), var(--gold-dark));
  }

  .person-name {
    position: absolute; left: 362px; top: 82px;
    font-family: "Allura", cursive; font-size: 52px; color: var(--gold-mid);
    white-space: nowrap;
  }
  .person-title {
    position: absolute; left: 364px; top: 161px;
    font-size: 15.5px; color: var(--text-grey);
  }

  .contact-list {
    position: absolute; left: 364px; top: 219px; list-style: none;
  }
  .contact-list li {
    display: flex; align-items: center; gap: 7px;
    height: 24px; font-size: 14px; color: var(--text-grey); white-space: nowrap;
  }
  .contact-icon { width: 15px; height: 15px; flex: none; }

  .strapline {
    position: absolute; left: 0; right: 0; top: 324px; height: 32px;
    background: linear-gradient(90deg, var(--gold-dark), var(--gold-light));
    color: #fff; font-weight: 500; font-size: 19.5px; letter-spacing: 0.4px;
    display: flex; align-items: center; justify-content: center; white-space: nowrap;
  }
</style>
</head>
<body>
  <section class="card card-front">
    <div class="front-wordmark">Fern Mentoring</div>
  </section>

  <section class="card card-back">
    <div class="back-wordmark">Fern Mentoring</div>

    <div class="social-row">
      <span class="social-dot"></span>
      <span class="social-dot"></span>
      <span class="social-dot"></span>
      <span class="social-handle">@fernmentoringAU</span>
    </div>

    <div class="divider"></div>
    <div class="divider-accent"></div>

    <div class="person-name">Greta Pellham</div>
    <div class="person-title">Business &amp; Personal Coach</div>

    <ul class="contact-list">
      <li>
        <svg class="contact-icon" viewBox="0 0 16 16" aria-hidden="true">
          <circle cx="8" cy="8" r="8" fill="#d99a2a"/>
          <path d="M5.2 4.2l1.6-.2.8 2-1 .8a5 5 0 0 0 2.6 2.6l.8-1 2 .8-.2 1.6c-3.8.4-7-2.8-6.6-6.6z" fill="#fff"/>
        </svg>
        +61 (0)491 570 156
      </li>
      <li>
        <svg class="contact-icon" viewBox="0 0 16 16" aria-hidden="true">
          <circle cx="8" cy="8" r="8" fill="#d99a2a"/>
          <rect x="4" y="5.2" width="8" height="5.6" rx="0.6" fill="#fff"/>
          <path d="M4.3 5.6L8 8.4l3.7-2.8" fill="none" stroke="#d99a2a" stroke-width="0.9"/>
        </svg>
        greta@fernmentoring-example.com.au
      </li>
      <li>
        <svg class="contact-icon" viewBox="0 0 16 16" aria-hidden="true">
          <circle cx="8" cy="8" r="8" fill="#d99a2a"/>
          <circle cx="8" cy="8" r="4" fill="none" stroke="#fff" stroke-width="1"/>
          <path d="M4 8h8M8 4c-1.6 2.4-1.6 5.6 0 8M8 4c1.6 2.4 1.6 5.6 0 8" fill="none" stroke="#fff" stroke-width="0.8"/>
        </svg>
        www.fernmentoring-example.com.au
      </li>
    </ul>

    <div class="strapline">A steady partner to help you find clarity and focus</div>
  </section>
</body>
</html>
```